Irrigation Business needs their business cards modernised and revamped

I would like to keep my current logo, colours and revamp the format of the card.

I would like the card to be clean yet important.

Im not sure if you include texture but i would like the named logo to be indented into the card etc.

show me something alive and free something thats clinical to the point yet has a feel of achievement. i would like people to go nice card.

Target Market(s)

high end clients, corporate, sports field manger, the guys that make the decisions

Industry/Entity Type

Business

Contact Information for Business Card

nformation to be included

Dean Harlow (Director)
0487305526
dean@kolvat.biz
www.kestonfieldworks.com

instagram logo
google logo
facebook logo

Colors

Designer to choose colors to be used in the design.

Requirements
Nice to have
• indentations a really nice feel to the card good texture

```html
<!DOCTYPE html>
<html lang="en">
<head>
<meta charset="utf-8">
<title>Keston Fieldworks – Business Card</title>
<link href="https://fonts.googleapis.com/css2?family=Lato:wght@400;700;900&display=swap" rel="stylesheet">
<style>
  :root {
    --page: #e9e6e1;
    --card-dark: #2a2a2c;
    --card-dark-edge: #333336;
    --card-light: #fbfbfa;
    --brand-blue: #2f6fc0;
    --brand-sky: #35a6dc;
    --brand-deep: #1f4f93;
    --brand-green: #2fae5a;
    --ink: #4a4a4c;
  }
  * { box-sizing: border-box; margin: 0; padding: 0; }
  html, body { width: 1200px; height: 800px; overflow: hidden; }
  body {
    background: var(--page);
    font-family: "Lato", sans-serif;
    display: flex;
    align-items: center;
    justify-content: center;
    gap: 40px;
  }
  .card {
    width: 540px;
    height: 310px;
    border-radius: 18px;
    position: relative;
    overflow: hidden;
  }
  /* Front */
  .card-front {
    background: radial-gradient(circle at 50% 50%, var(--card-dark-edge), var(--card-dark) 70%);
    display: flex;
    flex-direction: column;
    align-items: center;
    justify-content: center;
    gap: 18px;
  }
  .brand-dot {
    border-radius: 50%;
    background: linear-gradient(135deg, var(--brand-sky), var(--brand-deep));
  }
  .card-front .brand-dot { width: 92px; height: 92px; }
  .brand-name {
    color: var(--brand-blue);
    font-weight: 900;
    text-transform: uppercase;
    letter-spacing: 1px;
    white-space: nowrap;
  }
  .card-front .brand-name { font-size: 38px; }

  /* Back */
  .card-back { background: var(--card-light); }
  .back-brand {
    position: absolute;
    top: 30px;
    right: 32px;
    display: flex;
    align-items: center;
    gap: 10px;
  }
  .back-brand .brand-dot { width: 40px; height: 40px; }
  .back-brand .brand-name { font-size: 19px; }

  .person {
    position: absolute;
    top: 118px;
    left: 34px;
    padding-left: 16px;
    border-left: 10px solid var(--brand-sky);
  }
  .person-name { font-size: 26px; font-weight: 400; color: var(--ink); line-height: 1.05; }
  .person-role { font-size: 13px; font-weight: 400; color: var(--brand-blue); }

  .contact-list {
    position: absolute;
    left: 34px;
    top: 196px;
    list-style: none;
    display: flex;
    flex-direction: column;
    gap: 6px;
  }
  .contact-item {
    display: flex;
    align-items: center;
    gap: 9px;
    font-size: 15px;
    color: var(--ink);
  }
  .contact-item svg { width: 15px; height: 15px; fill: var(--brand-green); }

  .social-row {
    position: absolute;
    right: 34px;
    top: 216px;
    display: flex;
    gap: 12px;
  }
  .social-tile { width: 16px; height: 16px; background: var(--brand-blue); border-radius: 2px; }

  .rule {
    position: absolute;
    left: 34px;
    right: 34px;
    top: 252px;
    height: 3px;
    background: linear-gradient(90deg, var(--brand-sky), var(--brand-blue));
  }
  .website {
    position: absolute;
    left: 34px;
    top: 262px;
    font-size: 15px;
    font-weight: 700;
    color: var(--brand-deep);
  }
</style>
</head>
<body>
  <section class="card card-front">
    <div class="brand-dot"></div>
    <div class="brand-name">Keston Fieldworks</div>
  </section>

  <section class="card card-back">
    <div class="back-brand">
      <div class="brand-dot"></div>
      <div class="brand-name">Keston Fieldworks</div>
    </div>

    <div class="person">
      <div class="person-name">Dean Harlow</div>
      <div class="person-role">Director</div>
    </div>

    <ul class="contact-list">
      <li class="contact-item">
        <svg viewBox="0 0 16 16" aria-hidden="true"><path d="M3 1h3l1.5 4-2 1.3a9 9 0 0 0 4.2 4.2L11 8.5l4 1.5v3a2 2 0 0 1-2 2A13 13 0 0 1 1 3a2 2 0 0 1 2-2z"/></svg>
        <span>0487305526</span>
      </li>
      <li class="contact-item">
        <svg viewBox="0 0 16 16" aria-hidden="true"><path d="M1 3h14v10H1z M1 3l7 6 7-6" fill="none" stroke="#2fae5a" stroke-width="1.6"/></svg>
        <span>dean@kolvat.biz</span>
      </li>
    </ul>

    <div class="social-row">
      <span class="social-tile"></span>
      <span class="social-tile"></span>
      <span class="social-tile"></span>
    </div>

    <div class="rule"></div>
    <div class="website">www.kestonfieldworks.com</div>
  </section>
</body>
</html>
```